Business Card for a mobile physiotherapy company

I need a layout for a business card for a mobile physiotherapy company.
Slogan is "Mobile Physiotherapy - Your Road To Recovery"
Phone number is 867-555-0142
Email VardenTherapy@postnest.ca (subject to change with website)
Website www.VardenTherapy.ca
My name and credentials: Luke Varden Luke Varden, BSc(kin), MPT, CAFCI, IMS
Information maybe included: Direct Billing, Services including Physiotherapy, IMS, acupuncture
Maybe include facebook and instagram logos
One side with the logo clean and sharp
Other side with details, try not to look too busy, keep everything concise

```html
<!DOCTYPE html>
<html lang="en">
<head>
<meta charset="utf-8">
<title>Varden Therapy Business Card</title>
<link href="https://fonts.googleapis.com/css2?family=Source+Sans+3:ital,wght@0,400;0,600;0,700;1,400&display=swap" rel="stylesheet">
<style>
  :root {
    --backdrop: #2a2a2a;
    --navy: #2d4a72;
    --forest: #0d5148;
    --paper: #ffffff;
  }
  * { box-sizing: border-box; margin: 0; padding: 0; }
  html, body {
    width: 1125px; height: 1200px; overflow: hidden;
    background: var(--backdrop);
    font-family: "Source Sans 3", "Myriad Pro", sans-serif;
  }
  .card {
    position: absolute; left: 150px; width: 824px; height: 470px;
    overflow: hidden;
  }
  .card-front { top: 106px; background: var(--paper); }
  .card-back { top: 638px; background: var(--forest); color: var(--paper); }

  .front-bands { position: absolute; inset: 0; width: 100%; height: 100%; }

  .brand-name {
    position: absolute; left: 0; right: 0; top: 150px;
    text-align: center; color: var(--navy);
    font-size: 56px; font-weight: 700; letter-spacing: 3px;
    text-transform: uppercase;
  }

  .person {
    position: absolute; left: 42px; top: 338px; color: var(--paper);
  }
  .person-name { font-size: 29px; font-weight: 700; line-height: 1.1; }
  .person-credentials, .person-note { font-size: 21px; font-weight: 600; line-height: 1.3; }

  .contact-list {
    position: absolute; right: 42px; top: 342px; list-style: none;
    color: var(--paper); font-size: 20px; line-height: 27px; text-align: right;
  }
  .contact-list li { display: flex; justify-content: flex-end; align-items: center; gap: 10px; }
  .contact-icon { width: 20px; height: 20px; fill: var(--paper); }

  .social-dots { position: absolute; right: 40px; top: 36px; display: flex; gap: 4px; }
  .social-dot { width: 37px; height: 37px; border-radius: 50%; background: var(--paper); }

  .back-brand {
    position: absolute; left: 0; right: 0; top: 190px; text-align: center;
    font-size: 60px; font-weight: 700; letter-spacing: 3px; text-transform: uppercase;
  }
  .tagline {
    position: absolute; left: 0; right: 0; top: 374px; text-align: center;
    font-size: 21px; font-style: italic;
  }
  .services {
    position: absolute; left: 0; right: 0; top: 403px; text-align: center;
    font-size: 21px;
  }
  .services .sep { font-size: 14px; margin: 0 6px; vertical-align: middle; }
</style>
</head>
<body>

<section class="card card-front">
  <svg class="front-bands" viewBox="0 0 824 470" preserveAspectRatio="none" aria-hidden="true">
    <polygon points="0,211 419,372 824,198 824,470 0,470" fill="var(--navy)"/>
    <polygon points="62,234 419,362 762,231 419,375" fill="var(--forest)"/>
  </svg>

  <div class="brand-name">Varden Therapy</div>

  <div class="person">
    <div class="person-name">LUKE VARDEN</div>
    <div class="person-credentials">BSc(kin), MPT, CAFCI, IMS</div>
    <div class="person-note">Direct Billing</div>
  </div>

  <ul class="contact-list">
    <li>867-555-0142
      <svg class="contact-icon" viewBox="0 0 20 20" aria-hidden="true"><path d="M2 7c0-3 4-4 8-4s8 1 8 4v2h-4V7H6v2H2z M5 10h10l2 7H3z"/></svg>
    </li>
    <li>VardenTherapy@postnest.ca
      <svg class="contact-icon" viewBox="0 0 20 20" aria-hidden="true"><path d="M1 4h18v2l-9 6-9-6z M1 8l9 6 9-6v8H1z"/></svg>
    </li>
    <li>www.VardenTherapy.ca
      <svg class="contact-icon" viewBox="0 0 20 20" aria-hidden="true"><circle cx="10" cy="10" r="9"/><path d="M5 6h4l1 3-3 2 1 5-3-3z M12 4l4 3-2 3-3-1z" fill="var(--navy)"/></svg>
    </li>
  </ul>
</section>

<section class="card card-back">
  <div class="social-dots" aria-label="Social media links">
    <span class="social-dot"></span>
    <span class="social-dot"></span>
  </div>

  <div class="back-brand">Varden Therapy</div>

  <p class="tagline">Mobile Physiotherapy - Your Road To Recovery</p>
  <p class="services">Physiotherapy<span class="sep">●</span>IMS<span class="sep">●</span>Acupuncture</p>
</section>

</body>
</html>
```